Brightmill Data Works

Our company is about IT hardwares and IT solutions. IT hardware such as PC, RAMS, storage and servers. IT solutions such as project management, BA. We are also selling new technology too.

Target Market(s)

Consumer, Small to Medium Business, Corporate

Requirements
Must have
• The business card must have the following:
• Name:
• Title:
• Contact Number:
• Email address:
• Website:
• Color: Must match the logo color upgrade

```html
<!DOCTYPE html>
<html lang="en">
<head>
<meta charset="utf-8">
<title>Brightmill Data Works – Business Card</title>
<link rel="stylesheet" href="https://fonts.googleapis.com/css2?family=Ubuntu:wght@400;500;700&display=swap">
<style>
  :root {
    --page-bg: #e9e6e3;
    --orange-light: #d38c37;
    --orange-deep: #bb6224;
    --accent: #d98a2e;
    --card-white: #fbfbfa;
    --ink: #3a3a3a;
    --ink-soft: #555555;
  }
  * { box-sizing: border-box; margin: 0; padding: 0; }
  html, body {
    width: 1200px; height: 997px; overflow: hidden;
    background: var(--page-bg);
    font-family: "Ubuntu", Arial, sans-serif;
  }
  .stage { position: relative; width: 1200px; height: 997px; }
  .card {
    position: absolute; width: 620px; height: 354px;
    border-radius: 3px;
    box-shadow: 0 10px 24px rgba(0,0,0,0.12), 0 2px 4px rgba(0,0,0,0.08);
    overflow: hidden;
  }
  .card-front {
    left: 290px; top: 110px;
    background: linear-gradient(120deg, var(--orange-light), var(--orange-deep));
    display: flex; flex-direction: column; align-items: center; justify-content: center;
    gap: 16px;
  }
  .brand-dot {
    width: 34px; height: 34px; border-radius: 50%;
    background: #ffffff;
  }
  .brand-name {
    color: #ffffff; font-weight: 700; font-size: 34px;
    letter-spacing: 1px; text-transform: uppercase;
  }
  .card-back {
    left: 290px; top: 530px;
    background: var(--card-white);
  }
  .circuit-band {
    position: absolute; left: 0; top: 0; width: 100%; height: 150px;
    background: linear-gradient(180deg, rgba(217,138,46,0.28), rgba(217,138,46,0.08) 70%, rgba(217,138,46,0));
  }
  .person {
    position: absolute; left: 40px; top: 236px;
  }
  .person-name {
    color: var(--accent); font-weight: 700; font-size: 22px;
    text-transform: uppercase; letter-spacing: 0.3px;
  }
  .person-title {
    color: var(--ink); font-weight: 500; font-size: 14px;
    text-transform: uppercase; margin-top: 3px;
  }
  .contact-list {
    position: absolute; right: 40px; top: 170px;
    list-style: none;
  }
  .contact-item {
    display: flex; align-items: center; gap: 8px;
    color: var(--ink-soft); font-size: 13px; line-height: 20px;
  }
  .contact-icon { width: 12px; height: 12px; flex: none; }
</style>
</head>
<body>
  <main class="stage">
    <section class="card card-front" aria-label="Card front">
      <span class="brand-dot"></span>
      <h1 class="brand-name">Brightmill Data Works</h1>
    </section>

    <section class="card card-back" aria-label="Card back">
      <div class="circuit-band" role="img" aria-label="Orange circuit-board line pattern hanging from the top edge"></div>

      <div class="person">
        <p class="person-name">Daniel Reyes</p>
        <p class="person-title">CEO/Founder</p>
      </div>

      <ul class="contact-list">
        <li class="contact-item">
          <svg class="contact-icon" viewBox="0 0 12 12" aria-hidden="true">
            <path fill="#d98a2e" d="M2.5 0.8 4.3 2.6 3.4 4a6 6 0 0 0 4.6 4.6l1.4-0.9 1.8 1.8-1.3 1.7C5 11 1 7 0.8 2.1z"/>
          </svg>
          555 204 7183
        </li>
        <li class="contact-item">
          <svg class="contact-icon" viewBox="0 0 12 12" aria-hidden="true">
            <rect x="0.5" y="2" width="11" height="8" rx="1" fill="#d98a2e"/>
            <path d="M1 2.8 6 6.6 11 2.8" fill="none" stroke="#fff" stroke-width="1"/>
          </svg>
          daniel@brightmilldata.com
        </li>
        <li class="contact-item">
          <svg class="contact-icon" viewBox="0 0 12 12" aria-hidden="true">
            <circle cx="6" cy="6" r="5.5" fill="#d98a2e"/>
            <path d="M0.8 6h10.4M6 0.6c-2.4 3-2.4 7.8 0 10.8M6 0.6c2.4 3 2.4 7.8 0 10.8" fill="none" stroke="#fff" stroke-width="0.8"/>
          </svg>
          www.brightmilldata.com
        </li>
      </ul>
    </section>
  </main>
</body>
</html>
```